TA BRAMLEY BUSINESS CARD DESIGN PROJECT

We need to utilize our logo that was expertly created on PixelHarbor and now need to match this with a business card design.

```html
<!DOCTYPE html>
<html lang="en">
<head>
<meta charset="utf-8">
<title>TA Bramley Business Card</title>
<link href="https://fonts.googleapis.com/css2?family=Open+Sans:wght@400;700&display=swap" rel="stylesheet">
<style>
  :root {
    --bg: #dcdddf;
    --paper: #efefed;
    --brand-blue: #0d56ad;
    --edge-blue: #0a4fc4;
    --ink-grey: #8a8a8a;
  }
  html, body {
    margin: 0;
    padding: 0;
    width: 1200px;
    height: 1051px;
    overflow: hidden;
    background: var(--bg);
    font-family: "Open Sans", sans-serif;
  }
  .card-set {
    position: absolute;
    top: 371px;
    left: 40px;
    display: flex;
    gap: 40px;
  }
  .card {
    position: relative;
    width: 540px;
    height: 309px;
    background: var(--paper);
    border-bottom: 4px solid var(--edge-blue);
    box-shadow: 0 14px 30px rgba(0,0,0,0.18);
    box-sizing: border-box;
  }
  .brand-name {
    position: absolute;
    margin: 0;
    font-weight: 700;
    color: var(--brand-blue);
    letter-spacing: 0.14em;
    white-space: nowrap;
  }
  .card--front .brand-name {
    top: 70px;
    left: 180px;
    font-size: 40px;
  }
  .card--back .brand-name {
    top: 126px;
    left: 0;
    width: 100%;
    text-align: center;
    font-size: 48px;
  }
  .holder {
    position: absolute;
    top: 196px;
    right: 330px;
    text-align: right;
  }
  .holder-name {
    margin: 0;
    font-size: 17px;
    font-weight: 700;
    color: var(--brand-blue);
    white-space: nowrap;
  }
  .holder-title {
    margin: 2px 0 0;
    font-size: 12px;
    color: var(--ink-grey);
  }
  .divider {
    position: absolute;
    top: 194px;
    left: 226px;
    width: 1px;
    height: 68px;
    background: var(--brand-blue);
  }
  .contact-list {
    position: absolute;
    top: 196px;
    left: 246px;
    margin: 0;
    padding: 0;
    list-style: none;
    font-size: 12.5px;
    color: var(--ink-grey);
  }
  .contact-list li {
    display: flex;
    align-items: center;
    gap: 7px;
    height: 21px;
  }
  .contact-list svg {
    width: 10px;
    height: 10px;
    fill: var(--brand-blue);
  }
</style>
</head>
<body>
  <main class="card-set">
    <section class="card card--front">
      <p class="brand-name">TA BRAMLEY</p>
      <div class="holder">
        <p class="holder-name">JONAS WHITFORD</p>
        <p class="holder-title">President</p>
      </div>
      <div class="divider"></div>
      <ul class="contact-list">
        <li>
          <svg viewBox="0 0 10 10" aria-hidden="true"><path d="M2 0.5 L3.6 2.6 L2.8 3.6 Q3.8 5.8 6.4 7.2 L7.4 6.4 L9.5 8 L8.3 9.5 Q4.5 9.2 1.6 5.6 Q0.2 3.6 0.6 1.6 Z"/></svg>
          555-014-2287
        </li>
        <li>
          <svg viewBox="0 0 10 10" aria-hidden="true"><path d="M0 2 H10 V8.5 H0 Z M0.6 2.4 L5 5.6 L9.4 2.4" stroke="#efefed" stroke-width="0.8"/></svg>
          j.whitford@tabramley.com
        </li>
        <li>
          <svg viewBox="0 0 10 10" aria-hidden="true"><circle cx="5" cy="5" r="4.8"/><path d="M0.5 5 H9.5 M5 0.3 Q2.4 5 5 9.7 M5 0.3 Q7.6 5 5 9.7" stroke="#efefed" stroke-width="0.7" fill="none"/></svg>
          www.tabramley.com
        </li>
      </ul>
    </section>
    <section class="card card--back">
      <p class="brand-name">TA BRAMLEY</p>
    </section>
  </main>
</body>
</html>
```